TalkHarbor - Language Coaching Services

Sleek, innovative, trendy design for Language Coaching business.

TalkHarbor is a new UK based company that provides Language Coaching services. We offer highly personalized on-line and face to face language courses. We also impart learning techniques workshops based on the latest neuroscience research for second-language acquisition.

Target Market(s)

See attached info

Industry/Entity Type

Consulting

Contact Information for Business Card

TalkHarbor
DaniaKV@talkharbor.co.uk
TalkHarbor.co.uk
London, UK

Font styles to use
Sans Serif

```html
<!DOCTYPE html>
<html lang="en">
<head>
<meta charset="utf-8">
<title>TalkHarbor – Business Card</title>
<link rel="stylesheet" href="https://fonts.googleapis.com/css2?family=Work+Sans:wght@400;500&display=swap">
<style>
  :root {
    --page-bg: #1c1c1e;
    --card-bg: #2a2a2c;
    --card-bg-dark: #232325;
    --ink-light: #f2f2f2;
    --ink-silver: #b9b9bc;
    --accent: #17a9e6;
  }
  * { margin: 0; padding: 0; box-sizing: border-box; }
  html, body { width: 1200px; height: 900px; overflow: hidden; background: var(--page-bg); }
  body { font-family: "Work Sans", Arial, sans-serif; color: var(--ink-light); position: relative; }

  .card {
    position: absolute;
    left: 270px;
    width: 660px;
    height: 377px;
    background: linear-gradient(135deg, var(--card-bg-dark), var(--card-bg) 60%, #303033);
    box-shadow: 0 12px 30px rgba(0,0,0,.55);
  }
  .card--front { top: 50px; }
  .card--back { top: 473px; }

  /* Front */
  .front-brand {
    position: absolute; left: 0; right: 0; top: 90px;
    display: flex; flex-direction: column; align-items: center; gap: 16px;
  }
  .brand-circle {
    width: 116px; height: 116px; border-radius: 50%;
    border: 7px solid var(--ink-silver);
  }
  .brand-name {
    font-weight: 400; font-size: 50px; letter-spacing: 3px;
    text-transform: uppercase; color: var(--ink-silver); line-height: 1;
    white-space: nowrap;
  }
  .front-web {
    position: absolute; left: 0; right: 0; bottom: 34px;
    text-align: center; font-size: 15px; letter-spacing: 1.5px; color: var(--ink-light);
  }
  .web-name { color: var(--accent); }

  /* Back */
  .back-brand {
    position: absolute; left: 20px; top: 92px; width: 320px;
    display: flex; flex-direction: column; align-items: center; gap: 14px;
  }
  .back-brand .brand-circle { border-color: var(--accent); width: 120px; height: 120px; }
  .back-brand .brand-name { color: var(--accent); font-size: 42px; letter-spacing: 2px; }

  .divider {
    position: absolute; left: 360px; top: 96px;
    width: 2px; height: 185px; background: var(--ink-light);
  }
  .details { position: absolute; left: 392px; top: 88px; width: 250px; }
  .person-name {
    font-size: 25px; font-weight: 500; letter-spacing: 2px;
    text-transform: uppercase; color: var(--accent); line-height: 1.1;
    white-space: nowrap;
  }
  .person-role { font-size: 16px; letter-spacing: 1.5px; margin-top: 4px; }
  .address { font-size: 16px; letter-spacing: 1.5px; line-height: 1.5; margin-top: 18px; font-style: normal; }
  .contact-list { list-style: none; margin-top: 12px; }
  .contact-list li {
    display: flex; align-items: center; gap: 10px;
    font-size: 16px; letter-spacing: 1.3px; line-height: 1.6;
    white-space: nowrap;
  }
  .contact-icon { width: 12px; height: 12px; flex: none; }
</style>
</head>
<body>

  <section class="card card--front" aria-label="Card front">
    <div class="front-brand">
      <div class="brand-circle"></div>
      <div class="brand-name">TalkHarbor</div>
    </div>
    <div class="front-web">www.<span class="web-name">talkharbor</span>.co.uk</div>
  </section>

  <section class="card card--back" aria-label="Card back">
    <div class="back-brand">
      <div class="brand-circle"></div>
      <div class="brand-name">TalkHarbor</div>
    </div>

    <div class="divider"></div>

    <div class="details">
      <div class="person-name">Owen Hartley</div>
      <div class="person-role">Director</div>
      <address class="address">48b Harbour Lane,<br>London, UK, E1 6AN</address>
      <ul class="contact-list">
        <li>
          <svg class="contact-icon" viewBox="0 0 12 12" aria-hidden="true">
            <path d="M3 1 L4.5 3.5 L3.5 4.8 Q4.8 7.3 7.2 8.5 L8.5 7.5 L11 9 L10 11 Q4 10.5 1 2 Z" fill="var(--accent)"/>
          </svg>
          <span class="contact-text">(020) 555-0147</span>
        </li>
        <li>
          <svg class="contact-icon" viewBox="0 0 12 12" aria-hidden="true">
            <rect x="1" y="2.5" width="10" height="7" fill="none" stroke="var(--accent)" stroke-width="1.2"/>
            <path d="M1 2.5 L6 6.5 L11 2.5" fill="none" stroke="var(--accent)" stroke-width="1.2"/>
          </svg>
          <span class="contact-text">info@talkharbor.co.uk</span>
        </li>
        <li>
          <svg class="contact-icon" viewBox="0 0 12 12" aria-hidden="true">
            <circle cx="6" cy="6" r="5" fill="none" stroke="var(--accent)" stroke-width="1.1"/>
            <ellipse cx="6" cy="6" rx="2.2" ry="5" fill="none" stroke="var(--accent)" stroke-width="1"/>
            <path d="M1 6 H11 M2 3.5 H10 M2 8.5 H10" stroke="var(--accent)" stroke-width="0.9"/>
          </svg>
          <span class="contact-text">www.<span class="web-name">talkharbor</span>.co.uk</span>
        </li>
      </ul>
    </div>
  </section>

</body>
</html>
```